Healthcare/Medical Consultant Company

QRN is a Healthcare Conultant Company. We help doctors manage the business side of their medical practice.
We already have a very basic world press design. We want an upgraded design that conveys partnership, healthcare expertise and healthcare innovation to our client. It needs to have a sleek, clean, modern and inclusive look. Pictures need need to convey diversity (including pictures of people of all races and shows both men and women working together in a healthcare environment to make it better). The Pictures on the home page should particularly illustrate diversity and Healthcare expertise. The company logo is blue and white but the site doesn’t have to follow the exact same theme but the logo needs to blend well with the chosen theme. The logo should ideally be in the header of the website. We would also like the following included in our website:

1. Pages should include: a home page, About Us page, Services page, Get a quote page, Contact Us page, Staff page(where we can add pictures and bio for staff).

2. The Drop down menu for services should have hyperlinks ( for each service)Leading to a page that provides detailed info about that specific service. Our services include: Revenue Cycle Management, Regulatory Compliance, Human Resources Management, & practice Management.

3. Links to social media should in the header or footer of each page.

4. Contact info should be in the footer of each page.

5. Clients should be an email to us from the contact page.

Target Market(s)

Physician Medical Practices

Industry/Entity Type

Medical

Coding

Coded - Design and coding required

Font styles to use
Sans Serif

Colors

Designer to choose colors to be used in the design.

Requirements
Must have
• See project description
Nice to have
• See project description

```html
<!DOCTYPE html>
<html lang="en">
<head>
<meta charset="utf-8">
<title>QRN Health Partners</title>
<link rel="stylesheet" href="https://fonts.googleapis.com/css2?family=Lato:wght@300;400;700;900&display=swap">
<style>
:root{
  --blue:#1557b0;
  --blue-deep:#0b3d86;
  --blue-dark:#082c66;
  --blue-light:#3d86d8;
  --ink:#3a3f47;
  --muted:#6b7380;
  --line:#d7dde6;
  --white:#ffffff;
  --bg:#f4f6f9;
}
*{box-sizing:border-box;margin:0;padding:0}
html,body{width:1200px;height:2928px;overflow:hidden}
body{font-family:"Lato",Arial,sans-serif;color:var(--ink);background:var(--white);position:relative}
a{color:inherit;text-decoration:none}

/* header */
.site-header{position:absolute;top:0;left:0;width:1200px;height:64px;background:var(--white);display:flex;align-items:center;justify-content:space-between;padding:0 150px 0 140px;box-shadow:0 2px 6px rgba(0,0,0,.06);z-index:5}
.brand{display:flex;flex-direction:column;color:var(--blue)}
.brand-name{font-weight:900;font-size:30px;letter-spacing:2px;line-height:1}
.brand-sub{font-size:10px;font-weight:400;letter-spacing:.5px;margin-top:3px}
.main-nav{display:flex;gap:30px;font-size:13px;font-weight:700;color:var(--ink)}
.main-nav .active{color:var(--blue);border-bottom:2px solid var(--blue);padding-bottom:4px}

/* hero */
.hero{position:absolute;top:64px;left:0;width:1200px;height:648px;overflow:hidden}
.hero-photo{position:absolute;inset:0;background:linear-gradient(110deg,#5d6f85 0%,#a7b6c6 35%,#e3e8ee 60%,#8fa3b8 100%)}
.hero-title{position:absolute;top:318px;left:0;width:100%;text-align:center;color:var(--white);text-shadow:0 2px 8px rgba(0,0,0,.35)}
.hero-title .kicker{font-size:34px;font-weight:400;letter-spacing:1px}
.hero-title .headline{font-size:54px;font-weight:700;letter-spacing:2px;margin-top:4px}
.hero-dots{position:absolute;top:565px;left:0;width:100%;display:flex;justify-content:center;gap:10px}
.hero-dots span{width:10px;height:10px;border-radius:50%;background:rgba(255,255,255,.6)}
.hero-dots span.on{background:var(--white)}
.hero-curve{position:absolute;left:0;bottom:0}

/* about */
.about{position:absolute;top:712px;left:0;width:1200px;height:320px;text-align:center}
.section-title{font-size:34px;font-weight:700;color:var(--blue);letter-spacing:1px}
.title-rule{width:54px;height:3px;background:var(--blue);margin:10px auto 0}
.about .section-title{margin-top:56px}
.about p{width:620px;margin:26px auto 0;font-size:15px;line-height:24px;color:var(--muted)}
.btn{display:inline-block;border:2px solid var(--blue);color:var(--blue);font-size:12px;font-weight:700;letter-spacing:1px;padding:9px 26px;border-radius:2px;background:var(--white)}
.about .btn{margin-top:24px}

/* services */
.services{position:absolute;top:1032px;left:0;width:1200px;height:548px;background:radial-gradient(ellipse at 50% 55%,var(--blue-light) 0%,var(--blue) 45%,var(--blue-deep) 100%);color:var(--white);overflow:hidden}
.services-curve{position:absolute;top:0;left:0}
.services .section-title{color:var(--white);text-align:center;margin-top:50px;font-size:26px}
.services .title-rule{background:var(--white)}
.service-ring{position:absolute;left:420px;top:130px}
.service-mark{position:absolute;left:0;top:228px;width:100%;text-align:center;font-size:92px;font-weight:900;letter-spacing:8px;color:var(--white)}
.service{position:absolute;width:300px;font-size:11px;line-height:15px}
.service h3{font-size:17px;font-weight:700;line-height:20px;margin-bottom:6px}
.service .more{display:block;margin-top:6px;font-size:10px;font-weight:700;letter-spacing:1px}
.service.left{text-align:right}
.service-icon{position:absolute;width:66px;height:66px;border-radius:50%;background:var(--white);display:flex;align-items:center;justify-content:center}

/* mission */
.mission{position:absolute;top:1580px;left:0;width:1200px;height:520px}
.mission-photo{position:absolute;inset:0;background:linear-gradient(100deg,#3d4752 0%,#6f7b86 30%,#c9d0d7 55%,#e8ecef 75%,#9aa7b3 100%)}
.mission-card{position:absolute;left:144px;top:148px;width:460px;background:var(--white);padding:28px 34px 34px;box-shadow:0 6px 20px rgba(0,0,0,.18)}
.mission-card h2{font-size:28px;font-weight:700;color:var(--blue)}
.mission-card .title-rule{margin:8px 0 0}
.mission-card p{font-size:13px;line-height:20px;color:var(--muted);margin-top:16px}
.mission-card .btn{margin-top:20px;padding:7px 22px;font-size:11px}

/* blogs */
.blogs{position:absolute;top:2100px;left:0;width:1200px;height:460px;text-align:center}
.blogs .section-title{margin-top:40px;font-size:30px}
.blog-list{position:absolute;top:140px;left:120px;display:flex;gap:72px;text-align:left}
.post{display:flex;gap:20px;width:420px}
.post-photo{width:140px;height:140px;border-radius:50%;flex:none}
.post-photo.one{background:linear-gradient(135deg,#d9e3ee,#8fa7c0)}
.post-photo.two{background:linear-gradient(135deg,#1a3d78,#5b8fd0)}
.post h3{font-size:17px;font-weight:700;color:var(--blue);line-height:21px;margin-top:10px}
.post p{font-size:12px;line-height:18px;color:var(--muted);margin-top:8px}
.post .more{display:block;margin-top:8px;font-size:10px;font-weight:700;letter-spacing:1px;color:var(--ink)}

/* footer */
.site-footer{position:absolute;top:2560px;left:0;width:1200px;height:368px;background:linear-gradient(180deg,var(--blue) 0%,var(--blue-deep) 100%);color:var(--white);overflow:hidden}
.footer-wave{position:absolute;top:0;left:0}
.footer-brand{position:absolute;left:140px;top:118px;font-size:64px;font-weight:900;letter-spacing:6px}
.footer-col{position:absolute;top:92px;font-size:13px;line-height:26px}
.footer-col h4{font-size:15px;font-weight:700;letter-spacing:1px;margin-bottom:6px}
.footer-col.links{left:408px}
.footer-col.contact{left:620px}
.footer-col.follow{left:900px}
.contact-row{display:flex;align-items:flex-start;gap:10px;line-height:20px;margin-bottom:6px}
.contact-row svg{flex:none;margin-top:3px}
.social{display:flex;gap:10px;margin-top:4px}
.social span{width:30px;height:30px;border-radius:50%;border:2px solid var(--white)}
.footer-bar{position:absolute;left:0;bottom:0;width:100%;height:48px;background:var(--blue-dark);display:flex;align-items:center;justify-content:center;font-size:12px;color:rgba(255,255,255,.8)}
</style>
</head>
<body>

<header class="site-header">
  <a class="brand" href="#">
    <span class="brand-name">QRN</span>
    <span class="brand-sub">QRN HEALTH PARTNERS LLC</span>
  </a>
  <nav class="main-nav">
    <a class="active" href="#">HOME</a>
    <a href="#">ABOUT US</a>
    <a href="#">SERVICES</a>
    <a href="#">GET A QUOTE</a>
    <a href="#">CONTACT US</a>
    <a href="#">STAFF</a>
  </nav>
</header>

<section class="hero">
  <div class="hero-photo" role="img" aria-label="Diverse team of doctors and clinicians gathered together reviewing work"></div>
  <div class="hero-title">
    <div class="kicker">QRN HEALTH PARTNERS</div>
    <div class="headline">ADVANCING HEALTHCARE</div>
  </div>
  <div class="hero-dots"><span class="on"></span><span></span><span></span><span></span></div>
  <svg class="hero-curve" width="1200" height="90" viewBox="0 0 1200 90">
    <path d="M0 40 Q600 110 1200 40 L1200 90 L0 90Z" fill="#ffffff"/>
    <path d="M0 40 Q600 110 1200 40" fill="none" stroke="#1557b0" stroke-width="4"/>
  </svg>
</section>

<section class="about">
  <h2 class="section-title">ABOUT QRN</h2>
  <div class="title-rule"></div>
  <p>QRN Health Partners (QRN) is a healthcare consulting firm skilled at helping physician practices advance their strategic vision in an ever-evolving healthcare system. QRN Health Partners specializes in revenue cycle optimization, practice management improvement and developing new physician practices.</p>
  <a class="btn" href="#">READ MORE</a>
</section>

<section class="services">
  <svg class="services-curve" width="1200" height="60" viewBox="0 0 1200 60">
    <path d="M0 0 L1200 0 L1200 10 Q600 70 0 10Z" fill="#ffffff"/>
  </svg>
  <h2 class="section-title">OUR SERVICES</h2>
  <div class="title-rule"></div>

  <svg class="service-ring" width="360" height="360" viewBox="0 0 360 360">
    <circle cx="180" cy="180" r="150" fill="none" stroke="rgba(255,255,255,.35)" stroke-width="2"/>
    <circle cx="180" cy="180" r="110" fill="none" stroke="rgba(255,255,255,.2)" stroke-width="1.5"/>
  </svg>
  <div class="service-mark">QRN</div>

  <div class="service-icon" style="left:434px;top:148px">
    <svg width="34" height="34" viewBox="0 0 34 34" fill="none" stroke="#1557b0" stroke-width="2.5"><circle cx="17" cy="17" r="12"/><path d="M17 9v8l6 4"/></svg>
  </div>
  <div class="service-icon" style="left:700px;top:148px">
    <svg width="34" height="34" viewBox="0 0 34 34" fill="none" stroke="#1557b0" stroke-width="2.5"><rect x="7" y="5" width="20" height="24" rx="2"/><path d="M12 13h10M12 18h10M12 23h6"/></svg>
  </div>
  <div class="service-icon" style="left:434px;top:368px">
    <svg width="34" height="34" viewBox="0 0 34 34" fill="none" stroke="#1557b0" stroke-width="2.5"><path d="M17 4l11 4v8c0 7-5 12-11 14C11 28 6 23 6 16V8z"/><path d="M12 17l4 4 7-8"/></svg>
  </div>
  <div class="service-icon" style="left:700px;top:368px">
    <svg width="34" height="34" viewBox="0 0 34 34" fill="none" stroke="#1557b0" stroke-width="2.5"><circle cx="17" cy="12" r="6"/><path d="M6 29c1-7 6-10 11-10s10 3 11 10"/></svg>
  </div>

  <div class="service left" style="left:112px;top:148px">
    <h3>Revenue Cycle<br>Management</h3>
    Billing, coding and claims handled end to end so your practice is paid faster.
    <span class="more">READ MORE</span>
  </div>
  <div class="service" style="left:788px;top:148px">
    <h3>Practice Management</h3>
    Practical guidance on scheduling, staffing and workflow that keeps your clinic running smoothly.
    <span class="more">READ MORE</span>
  </div>
  <div class="service left" style="left:112px;top:368px">
    <h3>Regulatory &amp; Compliance<br>Management</h3>
    Stay ahead of changing rules with audits, policies and training built for physicians.
    <span class="more">READ MORE</span>
  </div>
  <div class="service" style="left:788px;top:368px">
    <h3>Human Resources<br>Management</h3>
    Hiring, onboarding and payroll support that lets your team focus on patient care.
    <span class="more">READ MORE</span>
  </div>
</section>

<section class="mission">
  <div class="mission-photo" role="img" aria-label="Healthcare professionals of different backgrounds meeting around a table"></div>
  <div class="mission-card">
    <h2>OUR MISSION</h2>
    <div class="title-rule"></div>
    <p>We partner with physician practices to simplify operations, strengthen compliance and grow revenue, so doctors can spend more time where it matters most: with patients.</p>
    <a class="btn" href="#">READ MORE</a>
  </div>
</section>

<section class="blogs">
  <h2 class="section-title">OUR BLOGS</h2>
  <div class="title-rule"></div>
  <div class="blog-list">
    <article class="post">
      <div class="post-photo one" role="img" aria-label="Doctor consulting with a patient"></div>
      <div>
        <h3>Mauris vel lacus vitae felis vestibulum volutpat</h3>
        <p>Simple steps to reduce claim denials and speed up reimbursement in your practice.</p>
        <span class="more">READ MORE</span>
      </div>
    </article>
    <article class="post">
      <div class="post-photo two" role="img" aria-label="Digital healthcare technology concept"></div>
      <div>
        <h3>Vivamus porttitor purus nisi eleifend libero a tempus</h3>
        <p>How new data tools are helping small practices make smarter staffing decisions.</p>
        <span class="more">READ MORE</span>
      </div>
    </article>
  </div>
</section>

<footer class="site-footer">
  <svg class="footer-wave" width="1200" height="60" viewBox="0 0 1200 60">
    <path d="M0 0 L1200 0 L1200 20 Q900 60 600 30 Q300 0 0 40Z" fill="#ffffff"/>
  </svg>
  <div class="footer-brand">QRN</div>

  <div class="footer-col links">
    <h4>QUICK LINKS</h4>
    <div>Home</div>
    <div>About Us</div>
    <div>Services</div>
    <div>Get a Quote</div>
    <div>Contact Us</div>
  </div>

  <div class="footer-col contact">
    <h4>CONTACT US</h4>
    <div class="contact-row">
      <svg width="14" height="16" viewBox="0 0 14 16"><path d="M7 0a6 6 0 0 1 6 6c0 4-6 10-6 10S1 10 1 6a6 6 0 0 1 6-6z" fill="#fff"/><circle cx="7" cy="6" r="2.2" fill="#1557b0"/></svg>
      <span>118 Harbor Lane Suite 300<br>Fairview, CA 90210</span>
    </div>
    <div class="contact-row">
      <svg width="14" height="14" viewBox="0 0 14 14"><path d="M3 0l3 3-2 2c1 2 3 4 5 5l2-2 3 3-2 3C6 14 0 8 0 3z" fill="#fff"/></svg>
      <span>(555) 014-2278</span>
    </div>
    <div class="contact-row">
      <svg width="14" height="12" viewBox="0 0 14 12"><rect x="0.5" y="0.5" width="13" height="11" fill="none" stroke="#fff"/><path d="M1 1l6 5 6-5" fill="none" stroke="#fff"/></svg>
      <span>info@qrnhealth.example</span>
    </div>
  </div>

  <div class="footer-col follow">
    <h4>FOLLOW US</h4>
    <div class="social" aria-label="Social media links"><span></span><span></span><span></span><span></span></div>
  </div>

  <div class="footer-bar">© 2019 QRN. All rights reserved. Terms of Use</div>
</footer>

</body>
</html>
```